Suds & Woofs 2nd Annual Fundraiser

I am a Realtor sponsoring the 2nd annual fundraiser on behalf of Allies of Cedar Hollow Animal Haven. Like the flyer to be professional yet fun and inviting. Please see the attached file below. The 1st annual flyer was fun but not as professional, modern or inviting as I would have liked it to be.
Target Market(s)
Dog lovers in Ponte Vedra, Ponte Vedra Beach and Nocatee Florida
Logo Text
Needed
Font styles to use
Other font styles liked:
- Font that fits the style of the fundraiser
Colors
886aae
abd036
Requirements
Must have
- Please see the attached flyer and photos.
- This will be the 2nd Annual on Saturday, April 27, 2019 from 10AM - 1PM. Same location: Pemberly Realty, 418 Harrowgate Ln. Ponte Vedra FL 32940

```html
<!DOCTYPE html>
<html lang="en">
<head>
<meta charset="utf-8">
<title>Suds &amp; Woofs Doggie Wash Extravaganza</title>
<link rel="stylesheet" href="https://fonts.googleapis.com/css2?family=Montserrat:wght@500;600;800;900&family=Dosis:wght@500;600&display=swap">
<style>
  :root {
    --purple: #886aae;
    --green: #abd036;
    --white: #ffffff;
    --photo-light: #c9a27a;
    --photo-dark: #8a7a6c;
  }
  * { margin: 0; padding: 0; box-sizing: border-box; }
  html, body { width: 846px; height: 1200px; overflow: hidden; background: var(--white); }
  .flyer { position: relative; width: 846px; height: 1200px; overflow: hidden; background: var(--white); }
  .bands { position: absolute; inset: 0; }
  .title-block { position: absolute; left: 25px; top: 100px; color: var(--white); font-family: "Montserrat", sans-serif; }
  .title-kicker { font-size: 30px; font-weight: 600; letter-spacing: 0.5px; line-height: 36px; }
  .title-name { font-size: 60px; font-weight: 900; line-height: 62px; letter-spacing: 0.5px; }
  .title-sub { font-size: 27px; font-weight: 600; line-height: 32px; letter-spacing: 0.3px; }
  .tagline { position: absolute; left: 0; top: 261px; width: 377px; height: 61px; background: var(--white);
    border-radius: 0 31px 31px 0; display: flex; align-items: center; padding-left: 28px;
    font-family: "Dosis", sans-serif; font-weight: 600; font-size: 27px; color: var(--purple); }
  .event-photo { position: absolute; left: 566px; top: 92px; width: 280px; height: 305px;
    background: linear-gradient(160deg, var(--photo-light), var(--photo-dark)); border-radius: 6px 0 0 6px; }
  .features { position: absolute; top: 511px; list-style: none; font-family: "Montserrat", sans-serif;
    font-weight: 800; font-size: 24.5px; color: var(--white); line-height: 34px; }
  .features-left { left: 40px; }
  .features-right { left: 546px; }
  .features li { display: flex; align-items: center; gap: 10px; white-space: nowrap; }
  .paw { width: 20px; height: 20px; flex: none; }
  .details { position: absolute; left: 0; top: 694px; width: 846px; text-align: center;
    font-family: "Dosis", sans-serif; font-weight: 600; font-size: 28px; line-height: 34px; color: var(--purple); }
  .when, .where { position: absolute; top: 884px; font-family: "Dosis", sans-serif; font-weight: 600;
    font-size: 27px; line-height: 35px; color: var(--green); white-space: nowrap; }
  .when { left: 39px; }
  .where { left: 322px; width: 496px; text-align: center; }
  .contact { position: absolute; top: 1042px; width: 360px; text-align: center; color: var(--white);
    font-family: "Montserrat", sans-serif; font-style: normal; font-weight: 600; font-size: 16px; line-height: 20.5px; }
  .contact-sponsor { left: 23px; }
  .contact-charity { left: 492px; }
  .badge { position: absolute; top: 1127px; height: 64px; background: var(--white);
    display: flex; align-items: center; justify-content: center; text-align: center;
    font-family: "Montserrat", sans-serif; font-weight: 600; font-size: 11px; line-height: 13px; color: var(--purple); padding: 4px; }
  .badge-sponsor { left: 147px; width: 104px; }
  .badge-charity { left: 643px; width: 68px; font-size: 9px; line-height: 11px; }
</style>
</head>
<body>
<main class="flyer">
  <svg class="bands" width="846" height="1200" viewBox="0 0 846 1200" aria-hidden="true">
    <rect x="0" y="0" width="846" height="240" fill="var(--purple)"/>
    <rect x="0" y="238" width="846" height="182" fill="var(--green)"/>
    <path fill="var(--white)" d="M0,402 q17.6,16 35.25,0 t35.25,0 t35.25,0 t35.25,0 t35.25,0 t35.25,0 t35.25,0 t35.25,0 t35.25,0 t35.25,0 t35.25,0 t35.25,0 t35.25,0 t35.25,0 t35.25,0 t35.25,0 t35.25,0 t35.25,0 t35.25,0 t35.25,0 t35.25,0 t35.25,0 t35.25,0 t35.25,0 V430 H0 Z"/>
    <path fill="var(--purple)" d="M0,478 q17.6,-16 35.25,0 t35.25,0 t35.25,0 t35.25,0 t35.25,0 t35.25,0 t35.25,0 t35.25,0 t35.25,0 t35.25,0 t35.25,0 t35.25,0 t35.25,0 t35.25,0 t35.25,0 t35.25,0 t35.25,0 t35.25,0 t35.25,0 t35.25,0 t35.25,0 t35.25,0 t35.25,0 t35.25,0 V652 q-17.6,16 -35.25,0 t-35.25,0 t-35.25,0 t-35.25,0 t-35.25,0 t-35.25,0 t-35.25,0 t-35.25,0 t-35.25,0 t-35.25,0 t-35.25,0 t-35.25,0 t-35.25,0 t-35.25,0 t-35.25,0 t-35.25,0 t-35.25,0 t-35.25,0 t-35.25,0 t-35.25,0 t-35.25,0 t-35.25,0 t-35.25,0 t-35.25,0 Z"/>
    <path fill="var(--green)" d="M0,1020 q17.6,-16 35.25,0 t35.25,0 t35.25,0 t35.25,0 t35.25,0 t35.25,0 t35.25,0 t35.25,0 t35.25,0 t35.25,0 t35.25,0 t35.25,0 t35.25,0 t35.25,0 t35.25,0 t35.25,0 t35.25,0 t35.25,0 t35.25,0 t35.25,0 t35.25,0 t35.25,0 t35.25,0 t35.25,0 V1200 H0 Z"/>
    <defs>
      <symbol id="paw-icon" viewBox="0 0 20 20">
        <ellipse cx="10" cy="13.5" rx="5" ry="4.2" fill="currentColor"/>
        <circle cx="4" cy="8" r="2.2" fill="currentColor"/>
        <circle cx="8" cy="4.5" r="2.2" fill="currentColor"/>
        <circle cx="12" cy="4.5" r="2.2" fill="currentColor"/>
        <circle cx="16" cy="8" r="2.2" fill="currentColor"/>
      </symbol>
    </defs>
  </svg>

  <header class="title-block">
    <p class="title-kicker">SECOND ANNUAL</p>
    <h1 class="title-name">SUDS &amp; WOOFS</h1>
    <p class="title-sub">DOGGIE WASH EXTRAVAGANZA</p>
  </header>

  <p class="tagline">A Family Fun Event for All Ages</p>

  <div class="event-photo" role="img" aria-label="Photo of a volunteer kneeling beside a tan dog in a red harness, next to a chalkboard event sign, under a drawn sun"></div>

  <ul class="features features-left">
    <li><svg class="paw"><use href="#paw-icon"/></svg>FREE Doggy Wash</li>
    <li><svg class="paw"><use href="#paw-icon"/></svg>Food &amp; Beverages</li>
    <li><svg class="paw"><use href="#paw-icon"/></svg>Vendors (FREE give-a-ways)</li>
  </ul>
  <ul class="features features-right">
    <li><svg class="paw"><use href="#paw-icon"/></svg>Raffle Drawing</li>
    <li><svg class="paw"><use href="#paw-icon"/></svg>Grand Prize</li>
    <li><svg class="paw"><use href="#paw-icon"/></svg>Donations Welcome</li>
  </ul>

  <section class="details">
    <p>To make a donation: https://www.socialpage.com/achah</p>
    <p>Click: DONATE</p>
    <p>All domestic breeds from puppies to seniors invited.</p>
    <p>Please be sure Furry Fido is tolerant of other dogs, crowds and bathing.</p>
  </section>

  <p class="when">Saturday, April 27, 2019<br>10 AM - 1 PM</p>
  <p class="where">Location: Pemberly Realty, 418 Harrowgate Ln.<br>Ponte Vedra FL 32940</p>

  <address class="contact contact-sponsor">
    Marissa Delacourt<br>Pemberly Realty Corp.<br>770.555.0142<br>marissad@pemberlyrealtycorp.com
  </address>
  <address class="contact contact-charity">
    Dana Whitfield<br>ACHAH<br>904.555.0187<br>dana-whitfield@mailnest.net
  </address>

  <div class="badge badge-sponsor">Marissa Delacourt</div>
  <div class="badge badge-charity">Cedar Hollow Animal Haven</div>
</main>
</body>
</html>
```